Wealth Education Business Needs Sharp Business Card Design

We need a business card design for a recently launched investor education business called Harbor Crest.

The final design should promote security, empowerment, self improvement and financial gain. The card will ideally promote the stature of the business.

For more information and colours please visit harborcrest.com.au

Target Market(s)

Corporate executives and high net worth individuals

Industry/Entity Type

Education

Contact Information for Business Card

```html
<!DOCTYPE html>
<html lang="en">
<head>
<meta charset="utf-8">
<title>Harbor Crest – Business Card</title>
<link rel="stylesheet" href="https://fonts.googleapis.com/css2?family=Exo+2:wght@400;500;600&display=swap">
<style>
  :root {
    --backdrop: #e9e6e1;
    --card-white: #f7f7f7;
    --charcoal: #3d3b3c;
    --sky-blue: #1b93d6;
    --teal: #2a9a96;
    --ink: #2e2d2e;
    --light-text: #f1f1f1;
    --muted-text: #cfcfcf;
  }
  * { box-sizing: border-box; margin: 0; padding: 0; }
  html, body {
    width: 1200px; height: 803px; overflow: hidden;
    background: var(--backdrop);
    font-family: "Exo 2", sans-serif;
  }
  .canvas { position: relative; width: 1200px; height: 803px; }
  .card {
    position: absolute; width: 560px; height: 320px;
    background: var(--card-white);
    box-shadow: 0 6px 18px rgba(0,0,0,0.18);
    overflow: hidden;
  }
  .card--front { left: 320px; top: 61px; }
  .card--back  { left: 320px; top: 422px; }
  .card-shapes { position: absolute; inset: 0; }

  .brand {
    position: absolute; left: 0;
    display: flex; align-items: center; justify-content: center; gap: 10px;
    font-family: "Exo 2", sans-serif; font-weight: 500;
    color: var(--ink); text-transform: uppercase; white-space: nowrap;
  }
  .brand-dot { border-radius: 50%; background: var(--teal); flex: none; }
  .card--front .brand { width: 488px; top: 136px; height: 48px; font-size: 34px; letter-spacing: 4px; }
  .card--front .brand-dot { width: 30px; height: 30px; }
  .card--back .brand { width: 262px; top: 145px; height: 30px; font-size: 18px; letter-spacing: 2px; gap: 8px; }
  .card--back .brand-dot { width: 18px; height: 18px; }

  .front-website {
    position: absolute; right: 26px; top: 28px;
    writing-mode: vertical-rl;
    color: var(--light-text); font-size: 11px; letter-spacing: 0.5px;
  }

  .holder { position: absolute; left: 292px; top: 82px; color: var(--light-text); }
  .holder-name { font-size: 21px; font-weight: 500; letter-spacing: 1.5px; text-transform: uppercase; }
  .holder-role { font-size: 8.5px; letter-spacing: 1px; text-transform: uppercase; color: var(--muted-text); margin-top: 3px; }

  .contact-list { position: absolute; left: 292px; top: 160px; list-style: none; }
  .contact-item {
    display: flex; align-items: center; gap: 8px;
    height: 24px; color: var(--light-text); font-size: 10px;
  }
  .contact-item--address { align-items: flex-start; line-height: 12px; padding-top: 1px; }
  .contact-icon { width: 16px; height: 16px; flex: none; }
</style>
</head>
<body>
<main class="canvas">

  <section class="card card--front" aria-label="Card front">
    <svg class="card-shapes" viewBox="0 0 560 320" aria-hidden="true">
      <path d="M488 36 Q488 0 524 0 L560 0 L560 320 L488 320 Z" fill="var(--charcoal)"/>
    </svg>
    <div class="brand"><span class="brand-dot"></span>Harbor Crest</div>
    <p class="front-website">www.harborcrest.com.au</p>
  </section>

  <section class="card card--back" aria-label="Card back">
    <svg class="card-shapes" viewBox="0 0 560 320" aria-hidden="true">
      <path d="M262 36 Q262 0 298 0 L560 0 L560 320 L262 320 Z" fill="var(--charcoal)"/>
      <path d="M486 0 L560 0 L560 320 L530 320 L530 40 Q530 0 486 0 Z" fill="var(--sky-blue)"/>
      <rect x="262" y="82" width="14" height="40" fill="var(--sky-blue)"/>
    </svg>

    <div class="brand"><span class="brand-dot"></span>Harbor Crest</div>

    <div class="holder">
      <p class="holder-name">Daniel Reyes</p>
      <p class="holder-role">General Manager</p>
    </div>

    <ul class="contact-list">
      <li class="contact-item">
        <svg class="contact-icon" viewBox="0 0 16 16" aria-hidden="true"><circle cx="8" cy="8" r="7" fill="none" stroke="currentColor"/><path d="M5.2 4.6 L6.6 4.4 L7.2 6 L6.4 6.8 Q7.2 8.6 9 9.6 L9.9 8.8 L11.4 9.4 L11.2 10.8 Q7.5 11 5.2 4.6 Z" fill="currentColor"/></svg>
        03 9412 5580
      </li>
      <li class="contact-item">
        <svg class="contact-icon" viewBox="0 0 16 16" aria-hidden="true"><circle cx="8" cy="8" r="7" fill="none" stroke="currentColor"/><rect x="5.8" y="4" width="4.4" height="8" rx="0.8" fill="none" stroke="currentColor"/><circle cx="8" cy="10.6" r="0.5" fill="currentColor"/></svg>
        03 9412 5581
      </li>
      <li class="contact-item">
        <svg class="contact-icon" viewBox="0 0 16 16" aria-hidden="true"><circle cx="8" cy="8" r="7" fill="none" stroke="currentColor"/><rect x="4.5" y="5.5" width="7" height="5" fill="none" stroke="currentColor"/><path d="M4.5 5.5 L8 8.4 L11.5 5.5" fill="none" stroke="currentColor"/></svg>
        daniel@harborcrest.com.au
      </li>
      <li class="contact-item">
        <svg class="contact-icon" viewBox="0 0 16 16" aria-hidden="true"><circle cx="8" cy="8" r="7" fill="none" stroke="currentColor"/><circle cx="8" cy="8" r="4" fill="none" stroke="currentColor" stroke-width="0.8"/><path d="M4 8 H12 M8 4 Q5.8 8 8 12 M8 4 Q10.2 8 8 12" fill="none" stroke="currentColor" stroke-width="0.8"/></svg>
        www.harborcrest.com.au
      </li>
      <li class="contact-item contact-item--address">
        <svg class="contact-icon" viewBox="0 0 16 16" aria-hidden="true"><circle cx="8" cy="8" r="7" fill="none" stroke="currentColor"/><path d="M8 12.2 Q5 8.8 5 7 A3 3 0 0 1 11 7 Q11 8.8 8 12.2 Z" fill="currentColor"/><circle cx="8" cy="7" r="1.1" fill="var(--charcoal)"/></svg>
        <span>42 Quay Road,<br>Level 3 North Wing</span>
      </li>
    </ul>
  </section>

</main>
</body>
</html>
```